Company for Pallets, Wooden (Export Boxes) and Custom PAcking solutions needs a vantrel design

We need a car wrap design for our vantrel. Our products are Pallets, Boxes, Custom Machine Packing as well as loading containers for our clients. On the moment we are thinking of a white background with some of our products on the side of the vehicle. Another idea is to put our adresses on the front doors. On the back of the vantrel we'd like to show our websites as well as an additional phrase. At the moment the idea is to put: "Your products - safely, fast and fast - around the world" In German this would be: "Your Products - Safe, Clean, Fast - Around the World" As our clients are almost exclusively German. The wording on the car would be as good as german.

Target Market(s)

B2B only. Most of our clients are manufacturing companies. They produce everything from coffee machines to heavy duty machinery for big platns such as refineries. Mostly we pack the equipment for international shipping.

Requirements
Must have
• We want to see our logo, our slogan ("We.Pack.Responsibility.") And some of our products on the vantrel. For Color please make sure it fits our logo. German language is mandatory.
Nice to have
• Maybe something that symbolizes our products guarantee safe shipping worldwide.
Should not have
• We are open to pretty much anything

```html
<!DOCTYPE html>
<html lang="de">
<head>
<meta charset="utf-8">
<title>LWK Industrieverpackungen – Fahrzeugbeschriftung</title>
<link rel="stylesheet" href="https://fonts.googleapis.com/css2?family=Open+Sans:wght@400;600;700&family=Ubuntu:wght@500;700&display=swap">
<style>
  :root{
    --page:#ffffff;
    --wrap-white:#f6f6f4;
    --wrap-edge:#dcdcd8;
    --ink:#4a4848;
    --ink-dark:#3a3838;
    --brown-dark:#6b4424;
    --wood:#c8914f;
    --wood-light:#e2b47a;
    --wood-pale:#efd6b0;
    --trim:#3b3b3b;
    --square:#c88a4a;
  }
  *{margin:0;padding:0;box-sizing:border-box}
  html,body{width:1200px;height:1200px;overflow:hidden;background:var(--page)}
  .canvas{position:relative;width:1200px;height:1200px;font-family:"Open Sans",sans-serif;color:var(--ink)}

  /* Side panel */
  .side-wrap{position:absolute;left:40px;top:70px;width:1120px;height:470px;
    background:var(--wrap-white);border:1px solid var(--wrap-edge);border-radius:18px;overflow:hidden}
  .side-photo{position:absolute;right:0;top:0;width:300px;height:360px;
    background:linear-gradient(160deg,var(--wood-pale) 0%,var(--wood-light) 55%,#d9cdbd 100%)}
  .side-fold{position:absolute;right:300px;top:0;width:60px;height:360px;
    background:linear-gradient(90deg,rgba(0,0,0,0) 0%,#c9c9c7 60%,#eeeeec 100%);
    clip-path:polygon(100% 0,100% 100%,40% 100%)}
  .side-band{position:absolute;left:0;right:0;top:360px;height:34px;
    background:linear-gradient(180deg,var(--wood-light),var(--wood) 60%,#a86f37)}
  .side-trim{position:absolute;left:0;right:0;top:394px;height:36px;background:var(--trim)}
  .side-foot{position:absolute;left:0;right:0;top:430px;height:40px;
    background:linear-gradient(180deg,var(--wood),#b07840);display:flex;align-items:center;
    padding-left:280px;gap:26px;font-family:"Ubuntu",sans-serif;font-weight:700;font-size:17px;color:var(--ink-dark)}
  .side-foot span::before{content:"";display:inline-block;width:7px;height:7px;background:var(--ink-dark);margin-right:7px;vertical-align:middle}

  .side-contact{position:absolute;left:210px;top:210px}
  .side-contact .address{font-weight:700;font-size:17px;line-height:1.3;color:var(--ink)}
  .side-contact .phone{font-family:"Ubuntu",sans-serif;font-weight:700;font-size:34px;color:var(--brown-dark);margin-top:14px;letter-spacing:.5px}

  .brand{display:flex;align-items:center;gap:16px}
  .brand .mark{width:62px;height:62px;background:var(--square)}
  .brand .name{font-weight:700;color:var(--ink)}
  .side-brand{position:absolute;left:460px;top:40px;text-align:left}
  .side-brand .name{font-size:110px;line-height:1}
  .descriptor{font-size:20px;color:var(--ink-dark)}
  .slogan{font-family:"Ubuntu",sans-serif;font-weight:700;color:var(--brown-dark)}
  .web{font-family:"Ubuntu",sans-serif;font-weight:700;color:var(--brown-dark)}
  .side-brand .descriptor{margin-top:20px;font-size:21px}
  .side-brand .slogan{font-size:22px;margin-top:6px}
  .side-brand .web{font-size:20px;margin-top:6px;padding-left:40px;letter-spacing:.5px}

  /* Rear panel */
  .rear-wrap{position:absolute;left:390px;top:600px;width:420px;height:540px;
    background:var(--wrap-white);border:1px solid var(--wrap-edge);border-radius:22px 22px 10px 10px;overflow:hidden}
  .rear-phone{position:absolute;left:50%;transform:translateX(-50%);top:0;width:250px;height:40px;
    background:var(--brown-dark);border-radius:0 0 8px 8px;color:#fff;font-family:"Ubuntu",sans-serif;
    font-weight:700;font-size:26px;text-align:center;line-height:40px}
  .rear-brand{position:absolute;left:40px;top:70px}
  .rear-brand .mark{width:80px;height:80px}
  .rear-brand .name{font-size:82px;line-height:1}
  .rear-brand .descriptor{margin:6px 0 0 96px;font-size:17px}
  .rear-slogan{position:absolute;left:0;right:0;top:200px;text-align:center;font-size:18px}
  .rear-address{position:absolute;left:0;right:0;top:255px;text-align:center;font-weight:700;font-size:15px;color:var(--ink)}
  .rear-lower{position:absolute;left:0;right:0;top:330px;bottom:0;
    background:linear-gradient(180deg,var(--wood-light),var(--wood) 70%,#a86f37)}
  .rear-web{position:absolute;left:0;top:10px;width:200px;height:30px;background:var(--brown-dark);
    color:#fff;font-size:18px;line-height:30px;padding-left:20px}
  .rear-list{position:absolute;left:20px;top:52px;list-style:none;font-family:"Ubuntu",sans-serif;font-weight:700;font-size:15px;color:var(--ink-dark);line-height:1.35}
  .rear-list li::before{content:"";display:inline-block;width:6px;height:6px;background:var(--ink-dark);margin-right:7px;vertical-align:middle}
  .rear-photo{position:absolute;right:0;top:0;width:150px;height:150px;
    background:linear-gradient(160deg,var(--wood-pale),#d8cbb8)}
  .rear-trim{position:absolute;left:0;right:0;bottom:0;height:40px;background:var(--trim)}
</style>
</head>
<body>
<main class="canvas">

  <section class="side-wrap" aria-label="Seitenansicht der Beschriftung">
    <div class="side-photo" role="img" aria-label="Gestapelte Holzpaletten und Exportkisten aus hellem Holz"></div>
    <div class="side-fold" aria-hidden="true"></div>
    <div class="side-band"></div>
    <div class="side-trim"></div>
    <div class="side-foot">
      <span>Ihre Waren</span><span>Stabil. Präzise. Pünktlich</span><span>Weltweit ans Ziel</span>
    </div>

    <div class="side-contact">
      <p class="address">Lindenweg 14<br>71234 Birkenfeld</p>
      <p class="phone">7351 208417</p>
    </div>

    <div class="side-brand">
      <div class="brand"><span class="mark"></span><span class="name">LWK</span></div>
      <p class="descriptor">Industrieverpackungen</p>
      <p class="slogan">Wir.Schützen.Werte</p>
      <p class="web">www.lwk-pack.de</p>
    </div>
  </section>

  <section class="rear-wrap" aria-label="Heckansicht der Beschriftung">
    <div class="rear-phone">7351 208417</div>
    <div class="rear-brand">
      <div class="brand"><span class="mark"></span><span class="name">LWK</span></div>
      <p class="descriptor">Industrieverpackungen</p>
    </div>
    <p class="rear-slogan slogan">Wir.Schützen.Werte</p>
    <p class="rear-address">Lindenweg 14 71234 Birkenfeld</p>
    <div class="rear-lower">
      <div class="rear-photo" role="img" aria-label="Holzpaletten und Exportkiste"></div>
      <p class="rear-web web">www.lwk-pack.de</p>
      <ul class="rear-list">
        <li>Ihre Waren</li>
        <li>Stabil. Präzise. Pünktlich</li>
        <li>Weltweit ans Ziel</li>
      </ul>
      <div class="rear-trim"></div>
    </div>
  </section>

</main>
</body>
</html>
```